Website Design for a holiday home letting busines

We require a redesign of our present website www.pinebrookstays.com. We want the website to stand out and look professional and clean to make holiday hunters want to book a caravan or lodge holiday with us. Our logo is red however we DO NOT want the website to be red. We want a natural colour scheme.

The final design should communicate that we are a professional company to book with.

On the home page we require;
Overview of company
Photo
Search box for holiday (check in)
Late Deals
Reviews
News

We would like the following pages designed; home page, available dates page, caravans page, content page.

The website should be responsive for smart phones. One website I do like is http://www.verdoliso.be/nl/

Target Market(s)

Families

Industry/Entity Type

Travel

Number of Pages Required

5+ page

Font styles to use
Serif

Requirements
Must have
• The project must be responsive for mobile phones and tablets.
• Ability to search for holiday home holidays
• We want a natural colour scheme.
Nice to have
• A style we like is http://www.verdoliso.be/nl/
Should not have
• Do not use red as a colour for the website. Our logo is red so this is the only time we want this used.

```html
<!DOCTYPE html>
<html lang="en">
<head>
<meta charset="utf-8">
<title>Pinebrook Stays – Caravans and Lodges</title>
<link href="https://fonts.googleapis.com/css2?family=PT+Sans:wght@400;700&family=PT+Serif:wght@400;700&display=swap" rel="stylesheet">
<style>
:root{
  --brand-red:#c8262c;
  --blue:#2179c9;
  --blue-dark:#1a5f9f;
  --footer-blue:#2a80cf;
  --text:#555b61;
  --title:#3d4247;
  --line:#e2e5e8;
  --green:#6d9a2d;
  --star:#e8a21c;
  --bg:#ffffff;
}
*{box-sizing:border-box;margin:0;padding:0}
html,body{width:818px;height:1200px;overflow:hidden;background:var(--bg)}
body{font-family:"PT Sans",Arial,sans-serif;color:var(--text);position:relative}
.site-header{height:42px;display:flex;align-items:center;padding:0 68px;justify-content:space-between}
.brand{display:flex;align-items:center;gap:7px;font-weight:700;font-size:19px;color:var(--brand-red)}
.brand-mark{width:16px;height:16px;border-radius:50%;background:var(--brand-red)}
.header-right{display:flex;align-items:center;gap:22px}
.phone small{display:block;font-size:8px;color:#888;text-transform:uppercase}
.phone strong{font-size:14px;color:var(--title)}
.questions{background:var(--brand-red);color:#fff;font-size:12px;font-weight:700;padding:7px 14px;border-radius:16px}
.main-nav{height:18px;display:flex;justify-content:center;gap:22px;font-size:9px;font-weight:700;letter-spacing:.4px;color:#6a7076;text-transform:uppercase;align-items:center}
.main-nav .active{color:var(--blue)}
.hero{height:92px;background:linear-gradient(180deg,#b9d6ec 0%,#dde8ef 55%,#c9d2c4 100%)}
.intro{padding:18px 68px 0}
.intro h1{font-family:"PT Serif",serif;font-size:15px;color:var(--blue);text-transform:uppercase;margin-bottom:10px}
.intro p{font-size:9.5px;line-height:1.5;margin-bottom:10px}
.homes{position:absolute;left:68px;top:280px;width:682px;display:grid;grid-template-columns:repeat(4,1fr);grid-auto-rows:155px}
.photo{background:linear-gradient(135deg,#c9b49a,#e9ddcb 55%,#a99073)}
.card{border:1px solid var(--line);padding:16px 14px;background:#fff}
.card h2{font-family:"PT Serif",serif;font-size:14px;color:var(--title);text-transform:uppercase;margin-bottom:8px;white-space:nowrap}
.card p{font-size:8.5px;line-height:1.45;margin-bottom:12px}
.card-foot{display:flex;align-items:center;justify-content:space-between}
.btn{background:var(--green);color:#fff;font-size:8px;padding:4px 8px;border-radius:2px}
.stars{color:var(--star);font-size:10px;letter-spacing:1px}
.site-footer{position:absolute;left:0;top:923px;width:818px;height:249px;background:var(--footer-blue);color:#fff;padding:24px 68px;display:flex;gap:40px}
.site-footer h3{font-family:"PT Serif",serif;font-size:16px;text-transform:uppercase;margin-bottom:14px}
.site-footer p{font-size:9px;line-height:1.5;margin-bottom:10px;color:#e3eef9}
.newsletter{width:230px}
.field{background:#fff;color:#888;font-size:8.5px;padding:6px 8px;width:170px;margin-bottom:8px;border-radius:2px}
.subscribe{display:inline-block;background:#f2b52a;color:#fff;font-size:9px;font-weight:700;padding:6px 14px;border-radius:2px}
.contact{width:200px}
.sitemap ul{list-style:none;columns:2;column-gap:50px;font-size:9px;line-height:2.2;color:#e3eef9}
.bottom-bar{position:absolute;left:0;top:1172px;width:818px;height:28px;background:var(--blue-dark);color:#cfe0f1;font-size:8px;display:flex;align-items:center;justify-content:space-between;padding:0 68px}
.social{display:flex;align-items:center;gap:8px}
.social i{width:13px;height:13px;border-radius:50%;background:#cfe0f1;display:block}
</style>
</head>
<body>
<header class="site-header">
  <div class="brand"><span class="brand-mark"></span>Pinebrook Stays</div>
  <div class="header-right">
    <div class="phone"><small>General Enquiries</small><strong>0800 555 0142</strong></div>
    <div class="questions">Questions?</div>
  </div>
</header>
<nav class="main-nav">
  <span>Home</span><span class="active">News</span><span>Reviews</span><span>Caravans &amp; Lodges</span><span>Permanent Homes</span><span>Alder Cove</span><span>Late Deals &amp; Offers</span><span>Contact Us</span>
</nav>
<div class="hero" role="img" aria-label="Holiday park photo with caravans under a blue sky"></div>

<section class="intro">
  <h1>Our caravans and lodges at Alder Cove Holiday Park</h1>
  <p>We own the caravans and one lakeside lodge at Alder Cove Holiday Park near Kelwick Bay. Our properties sleep at least 6 people, with some sleeping 8. All our vans and lodges come complete with a TV in the living room as well as DVD players. Some have added entertainment packages provided. Our families are warmly met with all the essentials you would require for your holiday.</p>
  <p>Our accommodation is listed as Lakeview (Rosewood), Rosewood 3 and Birchfield, Lakeside lodge (Larchmont Lodge) and Fernleigh Row (Fernleigh and Ashdown).</p>
</section>

<section class="homes">
  <div class="photo" role="img" aria-label="Caravan lounge interior"></div>
  <article class="card"><h2>The Larchmont</h2><p>The Larchmont sleeps six in a bright lakeside setting close to the beach.</p><div class="card-foot"><span class="btn">View details</span><span class="stars">★★★★★</span></div></article>
  <div class="photo" role="img" aria-label="Lodge living room with sofa"></div>
  <article class="card"><h2>The Fernleigh</h2><p>The Fernleigh offers space for families with a deck and modern kitchen.</p><div class="card-foot"><span class="btn">View details</span><span class="stars">★★★★★</span></div></article>

  <article class="card"><h2>The Ashdown</h2><p>The Ashdown is a cosy caravan a short walk from the park pool.</p><div class="card-foot"><span class="btn">View details</span><span class="stars">★★★★★</span></div></article>
  <div class="photo" role="img" aria-label="Caravan dining area"></div>
  <article class="card"><h2>The Rosewood</h2><p>The Rosewood has warm interiors and a view over the quiet lake.</p><div class="card-foot"><span class="btn">View details</span><span class="stars">★★★★★</span></div></article>
  <div class="photo" role="img" aria-label="Caravan kitchen interior"></div>

  <div class="photo" role="img" aria-label="Caravan lounge interior"></div>
  <article class="card"><h2>The Larchmont</h2><p>The Larchmont sleeps six in a bright lakeside setting close to the beach.</p><div class="card-foot"><span class="btn">View details</span><span class="stars">★★★★★</span></div></article>
  <div class="photo" role="img" aria-label="Lodge living room with sofa"></div>
  <article class="card"><h2>The Fernleigh</h2><p>The Fernleigh offers space for families with a deck and modern kitchen.</p><div class="card-foot"><span class="btn">View details</span><span class="stars">★★★★★</span></div></article>

  <article class="card"><h2>The Ashdown</h2><p>The Ashdown is a cosy caravan a short walk from the park pool.</p><div class="card-foot"><span class="btn">View details</span><span class="stars">★★★★★</span></div></article>
  <div class="photo" role="img" aria-label="Caravan dining area"></div>
  <article class="card"><h2>The Rosewood</h2><p>The Rosewood has warm interiors and a view over the quiet lake.</p><div class="card-foot"><span class="btn">View details</span><span class="stars">★★★★★</span></div></article>
  <div class="photo" role="img" aria-label="Caravan bedroom interior"></div>
</section>

<footer class="site-footer">
  <div class="newsletter">
    <h3>Newsletter Signup</h3>
    <p>Sign up to hear about late deals, offers and park news first.</p>
    <div class="field">Enter your Name</div>
    <div class="field">Enter your Email</div>
    <span class="subscribe">SUBSCRIBE</span>
  </div>
  <div class="contact">
    <h3>Contact Information</h3>
    <p>Pinebrook Stays, Alder Cove Holiday Park, Kelwick Bay. Call or email us any day for bookings.</p>
    <p>Tel: 0800 555 0142<br>hello@pinebrookstays.com</p>
  </div>
  <div class="sitemap">
    <h3>Sitemap</h3>
    <ul>
      <li>About Us</li><li>News</li><li>FAQ</li><li>2015 Holidays</li><li>Late Deals</li><li>Local Areas</li>
      <li>Contact Us</li><li>Booking</li><li>Privacy Policy</li><li>Booking Terms</li><li>News</li><li>Site Search</li>
    </ul>
  </div>
</footer>
<div class="bottom-bar">
  <span>Design by Pinebrook Stays. All Rights Reserved.</span>
  <div class="social"><span>Social Icons:</span><i></i><i></i><i></i><i></i><i></i></div>
</div>
</body>
</html>
```